Verodex business card

Business card for sustainable investment company called "Verodex". Verodex is an exchange platform selling carbon credits between buyers and sellers. Carbon Credits are an environmental commodity for reducing global carbon emissions.

the card should obviously have our logo and the theme should be sustainability/environment mixed with a trading platform.

Contact Information for Business Card

Logo, Name, Title, Phone, Email

Colors
0054AA
0677BA
7BADD7
CADEEF
E8F1F8
0094D4
00A9DD
6FCCEA
C7EBF8
E9F6FB
00AB8E
00BBA5
67D7C9
C6EFE9
E9F9F6
59FF00
82FF00
B8FF75
E3FFCB
F4FFEA

```html
<!DOCTYPE html>
<html lang="en">
<head>
<meta charset="utf-8">
<title>Verodex business card</title>
<link rel="stylesheet" href="https://fonts.googleapis.com/css2?family=Montserrat:wght@600&family=Open+Sans:wght@400;600;700&display=swap">
<style>
  :root {
    --stage: #232323;
    --card-navy: #142a50;
    --card-navy-light: #1c3d63;
    --white: #ffffff;
    --sky: #6fcCea;
    --azure: #0094d4;
    --blue: #4a8fd6;
    --cyan: #6fccea;
    --icon: #7badd7;
  }
  * { box-sizing: border-box; margin: 0; padding: 0; }
  html, body {
    width: 1200px; height: 780px; overflow: hidden;
    background: var(--stage);
  }
  .stage {
    position: relative; width: 1200px; height: 780px;
    display: flex; align-items: center; justify-content: center; gap: 40px;
  }
  .card {
    position: relative; width: 540px; height: 309px;
    border-radius: 18px; overflow: hidden;
    background:
      radial-gradient(circle at 22% 70%, var(--card-navy-light) 0%, rgba(28,61,99,0) 55%),
      var(--card-navy);
    box-shadow: 0 14px 30px rgba(0,0,0,0.55);
    font-family: "Open Sans", Arial, sans-serif;
    color: var(--white);
  }
  .card--back {
    background:
      radial-gradient(circle at 82% 35%, var(--card-navy-light) 0%, rgba(28,61,99,0) 50%),
      var(--card-navy);
  }
  .brand {
    position: absolute; display: flex; align-items: center; gap: 14px;
  }
  .brand__square {
    width: 30px; height: 30px; background: var(--cyan); border-radius: 3px;
  }
  .brand__name {
    font-family: "Montserrat", Arial, sans-serif; font-weight: 600;
    text-transform: uppercase; letter-spacing: 0.02em; color: var(--white);
  }
  .card--front .brand { left: 150px; top: 128px; }
  .card--front .brand__square { width: 40px; height: 40px; }
  .card--front .brand__name { font-size: 48px; }
  .card--back .brand { left: 32px; top: 36px; }
  .card--back .brand__name { font-size: 30px; }

  .person {
    position: absolute; right: 36px; top: 38px; text-align: right;
  }
  .person__name { font-size: 26px; font-weight: 700; line-height: 1.1; }
  .person__first {
    background: linear-gradient(90deg, var(--blue), var(--cyan));
    -webkit-background-clip: text; background-clip: text; color: transparent;
  }
  .person__title { font-size: 14px; margin-top: 4px; }
  .accent-bar {
    position: absolute; right: 0; top: 36px; width: 22px; height: 62px;
    background: linear-gradient(180deg, var(--blue), var(--cyan));
  }

  .address {
    position: absolute; left: 70px; top: 140px;
    font-size: 15px; line-height: 1.45;
  }
  .contacts {
    position: absolute; left: 70px; bottom: 28px;
    list-style: none; font-size: 15px; line-height: 1.5;
  }
  .contacts li { display: flex; align-items: center; gap: 10px; }
  .contacts svg { width: 16px; height: 16px; flex: none; }
</style>
</head>
<body>
<main class="stage">
  <section class="card card--front" aria-label="Card front">
    <div class="brand">
      <span class="brand__square" aria-hidden="true"></span>
      <span class="brand__name">Verodex</span>
    </div>
  </section>

  <section class="card card--back" aria-label="Card back">
    <div class="brand">
      <span class="brand__square" aria-hidden="true"></span>
      <span class="brand__name">Verodex</span>
    </div>

    <div class="person">
      <p class="person__name"><span class="person__first">Marta</span> Kovalenko</p>
      <p class="person__title">Managing Director</p>
    </div>
    <span class="accent-bar" aria-hidden="true"></span>

    <address class="address" style="font-style:normal">
      1480 Linden Ave. Suite<br>310 Harbor City, TX 75010
    </address>

    <ul class="contacts">
      <li>
        <svg viewBox="0 0 24 24" aria-hidden="true"><path fill="#7badd7" d="M6.6 10.8a15 15 0 0 0 6.6 6.6l2.2-2.2a1 1 0 0 1 1-.25 11.4 11.4 0 0 0 3.6.57 1 1 0 0 1 1 1V20a1 1 0 0 1-1 1A17 17 0 0 1 3 4a1 1 0 0 1 1-1h3.5a1 1 0 0 1 1 1c0 1.25.2 2.45.57 3.57a1 1 0 0 1-.25 1z"/></svg>
        (555) 214-6083
      </li>
      <li>
        <svg viewBox="0 0 24 24" aria-hidden="true"><rect x="2" y="5" width="20" height="14" rx="2" fill="none" stroke="#7badd7" stroke-width="2"/><path d="M3 6l9 7 9-7" fill="none" stroke="#7badd7" stroke-width="2"/></svg>
        info@verodex.com
      </li>
      <li>
        <svg viewBox="0 0 24 24" aria-hidden="true"><circle cx="12" cy="12" r="9" fill="none" stroke="#7badd7" stroke-width="2"/><ellipse cx="12" cy="12" rx="4" ry="9" fill="none" stroke="#7badd7" stroke-width="1.6"/><path d="M3 12h18" stroke="#7badd7" stroke-width="1.6"/></svg>
        www.verodex.com
      </li>
    </ul>
  </section>
</main>
</body>
</html>
```